CrestHornSupply.com

I need a new webdesign for a company in the San Jose/SF Bay area that showcases the financial benefits of buying used band instruments for junior high students.This would be opposed to the current and costly option of renting cheap quality instruments from the 2 or 3 local music stores that charge a monthly fee that over the years charges the buyer 3 or 4x over..
Instruments: focus in on Alto Sax, Trumpet, Flute, Clarinet, Trombone, Tenor Sax, Baritone
Target middle schools are Larkfield Middle School and Maple Middle School in San Jose, CA. Both have award winning band programs.
Files attached may or may not be important.
Tabs Needed and funtional
Contact
Shopping Cart
Select Instrument
Checkout
Add to Cart, etc.
Instuments
quantity, etc.
trade in your instrument/sell your instrument
ability to add or take away new instruments for sale. including pictures
Additional questions or info, feel free to ask
Updates
Hi Designers,
Project Deadline Extended
Reason: In the next week you will be receiving specific content that will be required to be had on the website.
New desigins are still welcome. Please continue to contact me if you have questions about your individual designs.
Thanks!
Crest Horn

```html
<!DOCTYPE html>
<html lang="en">
<head>
<meta charset="utf-8">
<title>Crest Horn — Used Band Instruments</title>
<link href="https://fonts.googleapis.com/css2?family=Oswald:wght@400;500;700&family=Open+Sans:wght@400&display=swap" rel="stylesheet">
<style>
  :root{
    --bg:#262626;
    --bg-dark:#1f1f1f;
    --panel:#2d2d2d;
    --panel-line:#3f3f3f;
    --red:#e8493b;
    --white:#f2f2f2;
    --grey:#9a9a9a;
    --grey-dark:#6e6e6e;
  }
  *{margin:0;padding:0;box-sizing:border-box}
  html,body{width:846px;height:1200px;overflow:hidden}
  body{background:radial-gradient(ellipse at 50% 30%,#2e2e2e,var(--bg) 70%,#1c1c1c);font-family:Arial,Helvetica,sans-serif;color:var(--grey);position:relative}
  .abs{position:absolute}
  .brand{left:88px;top:34px;font:700 52px/1 'Oswald',sans-serif;color:var(--red);letter-spacing:-1px}
  .util-links{left:440px;top:52px;display:flex;gap:16px;font-size:9px;color:var(--grey)}
  .util-links .active{color:var(--red)}
  .cart{left:696px;top:48px;display:flex;align-items:center;gap:8px;font:500 10px 'Oswald',sans-serif;color:var(--red)}
  .search{left:540px;top:76px;width:218px;height:27px;display:flex}
  .search-field{flex:1;background:#1d1d1d;border:1px solid #333}
  .search-btn{width:48px;background:var(--red);color:#fff;font:500 10px/27px 'Oswald',sans-serif;text-align:center;border:1px solid #ff7a6c}
  .main-nav{left:88px;top:131px;width:670px;height:57px;display:flex;border-top:1px solid #3a3a3a;background:linear-gradient(#202020,#474747);border-bottom:6px solid #8a8a8a}
  .main-nav a{flex:1;text-align:center;font:500 15px/50px 'Oswald',sans-serif;color:#fff;text-decoration:none;border-right:1px solid #2a2a2a}
  .main-nav a:last-child{border-right:0}
  .hero{left:88px;top:211px;width:670px;height:335px;background:#3a3a3a}
  .hero-photo{left:0;top:0;width:451px;height:316px;background:linear-gradient(135deg,#1a1a1a 0%,#5a1010 35%,#b0231c 55%,#6b4a2a 75%,#2a2a2a 100%)}
  .hero-side{left:451px;top:0;width:219px;height:316px;background:linear-gradient(#3a3633,#1f1d1c)}
  .hero-title{left:478px;top:179px;width:170px;font:500 14px/16px 'Oswald',sans-serif;color:#fff;text-transform:uppercase}
  .hero-text{left:478px;top:236px;width:165px;font-size:7.5px;line-height:11px;color:var(--red);text-transform:uppercase}
  .hero-more{left:478px;top:280px;font:500 8px 'Oswald',sans-serif;color:#fff}
  .hero-dots{left:0;top:316px;width:670px;height:19px;background:#4a4a4a;display:flex;justify-content:center;align-items:center;gap:3px}
  .hero-dots span{width:7px;height:7px;border-radius:50%;background:#fff}
  .hero-dots span.on{background:var(--red)}
  .categories{left:88px;top:575px;width:670px;display:flex;gap:8px}
  .category{width:105px;text-align:center}
  .category-thumb{width:105px;height:105px;border:4px solid #4a4a4a;background:#232323;padding:6px}
  .category-thumb div{width:100%;height:100%}
  .category.active .category-thumb{border-color:var(--red)}
  .category-name{margin-top:8px;font:500 15px 'Oswald',sans-serif;color:var(--red)}
  .category.active .category-name{color:#fff}
  .panel{top:732px;width:218px;height:332px;background:var(--panel);border:1px solid var(--panel-line);padding:12px 14px}
  .panel h3{font:500 10px 'Oswald',sans-serif;color:var(--grey);text-transform:uppercase;padding-bottom:10px;border-bottom:1px solid var(--panel-line)}
  .item{display:flex;gap:10px;height:87px;padding-top:10px;border-bottom:1px solid var(--panel-line)}
  .item-img{width:72px;height:58px;flex:none}
  .price{font:500 14px 'Oswald',sans-serif;color:var(--grey)}
  .item-title{font-size:8px;line-height:11px;color:var(--red);text-transform:uppercase;margin-top:2px}
  .item-date{font-size:7.5px;font-style:italic;color:var(--grey);margin-top:2px}
  .details{font:500 8px 'Oswald',sans-serif;color:#fff;margin-top:8px}
  .see-all{position:absolute;left:14px;bottom:14px;font:500 8px 'Oswald',sans-serif;color:var(--red)}
  .about-lead{font-size:8px;line-height:11.5px;color:var(--red);text-transform:uppercase;margin-top:12px}
  .about-body{font-size:7.6px;line-height:11.2px;color:var(--grey);margin-top:9px}
  .footer-nav{left:88px;top:1094px;display:flex;font:500 10px 'Oswald',sans-serif}
  .footer-nav a{color:var(--grey);text-decoration:none;padding:0 13px;border-right:1px solid #444;line-height:20px}
  .footer-nav a:first-child{padding-left:0;color:var(--red)}
  .footer-nav a:last-child{border-right:0}
  .to-top{left:748px;top:1092px}
  .footer-rule{left:88px;top:1122px;width:670px;height:1px;background:#3c3c3c}
  .copyright{left:88px;top:1136px;font:400 10px 'Open Sans',sans-serif;color:var(--grey)}
</style>
</head>
<body>
  <div class="abs brand">Crest Horn</div>

  <div class="abs util-links"><span class="active">Register</span><span>Login</span><span>Delivery</span><span>Checkout</span><span>My Account</span></div>
  <div class="abs cart">
    <svg width="20" height="16" viewBox="0 0 20 16"><path d="M2 6h16l-2 9H4z" fill="#fff"/><path d="M6 6l4-5 4 5" stroke="#fff" stroke-width="1.5" fill="none"/></svg>
    CART: <span style="color:#fff">0</span>
  </div>
  <div class="abs search"><div class="search-field"></div><div class="search-btn">SEARCH</div></div>

  <nav class="abs main-nav"><a>HOME</a><a>ABOUT</a><a>FEATURED</a><a>STORE</a><a>NEWS</a><a>CONTACTS</a></nav>

  <section class="abs hero">
    <div class="abs hero-photo" role="img" aria-label="Close-up of a gloved hand playing a red electric guitar"></div>
    <div class="abs hero-side" role="img" aria-label="Dark blurred continuation of the guitar photo"></div>
    <div class="abs hero-title" style="left:390px;top:179px">Lorem ipsum dolor sit amet conse ctetur adipis-icing elit</div>
    <div class="abs hero-text" style="left:390px;top:236px">Lorem ipsum dolor sit amet conse ctetur adipisicing elit, sed do eius-mod tempor incididunt.</div>
    <div class="abs hero-more" style="left:390px;top:280px">READ MORE</div>
    <div class="abs hero-dots"><span class="on"></span><span></span><span></span><span></span><span></span></div>
  </section>

  <div class="abs categories">
    <div class="category active"><div class="category-thumb"><div role="img" aria-label="Bass drum" style="background:radial-gradient(circle,#eee 35%,#b22 45%,#2a2a2a 70%)"></div></div><div class="category-name">Lorem</div></div>
    <div class="category"><div class="category-thumb"><div role="img" aria-label="Red grand piano" style="background:radial-gradient(circle,#c9221a 30%,#232323 65%)"></div></div><div class="category-name">Ipsum</div></div>
    <div class="category"><div class="category-thumb"><div role="img" aria-label="MIDI keyboard controller" style="background:radial-gradient(circle,#555 30%,#232323 65%)"></div></div><div class="category-name">Dolor</div></div>
    <div class="category"><div class="category-thumb"><div role="img" aria-label="Red floor tom drum" style="background:radial-gradient(circle,#d42a20 30%,#232323 65%)"></div></div><div class="category-name">Sitem</div></div>
    <div class="category"><div class="category-thumb"><div role="img" aria-label="Red electric guitar" style="background:radial-gradient(circle,#a81e1a 25%,#232323 60%)"></div></div><div class="category-name">Amet</div></div>
    <div class="category"><div class="category-thumb"><div role="img" aria-label="Accordion" style="background:radial-gradient(circle,#b33a22 30%,#7a5a30 45%,#232323 70%)"></div></div><div class="category-name">Consectetuer</div></div>
  </div>

  <section class="abs panel" style="left:88px">
    <h3>Recent used products</h3>
    <div class="item"><div class="item-img" role="img" aria-label="Accordion" style="background:radial-gradient(circle,#666,#2d2d2d 70%)"></div><div><div class="price">$25.89</div><div class="item-title">Lorem ipsum dolor sit amet conse ctetur</div><div class="details">DETAILS ▸</div></div></div>
    <div class="item"><div class="item-img" role="img" aria-label="Acoustic guitar" style="background:radial-gradient(circle,#a0501c,#2d2d2d 70%)"></div><div><div class="price">$25.89</div><div class="item-title">Ipsum dolor sit amet conse ctetur</div><div class="details">DETAILS ▸</div></div></div>
    <div class="item" style="border-bottom:1px solid var(--panel-line)"><div class="item-img" role="img" aria-label="Instrument case" style="background:radial-gradient(circle,#333,#2d2d2d 70%)"></div><div><div class="price">$25.89</div><div class="item-title">Lorem ipsum dolor</div><div class="details">DETAILS ▸</div></div></div>
    <div class="see-all">SEE ALL</div>
  </section>

  <section class="abs panel" style="left:314px">
    <h3>Latest from the blog</h3>
    <div class="item"><div class="item-img" role="img" aria-label="Red keyboard" style="background:radial-gradient(circle,#c8261e,#2d2d2d 70%)"></div><div><div class="item-title">Lorem ipsum dolor sit amet conse ctetur</div><div class="item-date">25 December, 2012</div><div class="details">DETAILS ▸</div></div></div>
    <div class="item"><div class="item-img" role="img" aria-label="Tabla drum" style="background:radial-gradient(circle,#8a6a3a,#2d2d2d 70%)"></div><div><div class="item-title">Dolor sit amet conse ctetur</div><div class="item-date">25 December, 2012</div><div class="details">DETAILS ▸</div></div></div>
    <div class="item"><div class="item-img" role="img" aria-label="Shaker ball" style="background:radial-gradient(circle,#a8202a,#2d2d2d 70%)"></div><div><div class="item-title">Lorem ipsum dolor sit amet conse</div><div class="item-date">25 December, 2012</div><div class="details">DETAILS ▸</div></div></div>
    <div class="see-all">SEE ALL</div>
  </section>

  <section class="abs panel" style="left:540px">
    <h3>About us</h3>
    <div class="about-lead">Lorem ipsum dolor sit amet conse ctetur adipisicing elit, sed do eiusmod tempor incididunt ut labore et dolore</div>
    <div class="about-body">Lorem ipsum dolor sit amet conse ctetur adipisicing elit, sed do eiusmod tempor incididunt ut labore et dolore magna aliqua. Ut enim ad minim veniam, quis nostrud exercitation ullamco laboris nisi ut aliquip ex ea commodo consequat. Duis aute irure dolor in reprehenderit in voluptate velit esse cillum dolore eu fugiat nulla pariatur.</div>
    <div class="about-body">Sit amet conse ctetur adipisicing elit, sed do eiusmod tempor incididunt ut labore et dolore magna aliqua. Ut enim ad minim veniam, quis nostrud exercitation ullamco laboris nisi ut aliquip ex ea commodo conse-quat. Duis aute irure dolor in reprehenderit in voluptate velit esse cillum dolore eu fugiat nulla pariatur. Sit amet conse ctetur adipisicing elit, sed do eiusmod tempor incididunt ut labore et dolore magna aliqua. Ut enim ad minim veniam.</div>
    <div class="see-all">READ MORE</div>
  </section>

  <nav class="abs footer-nav"><a>HOME</a><a>ABOUT</a><a>FEATURED</a><a>STORE</a><a>NEWS</a><a>CONTACTS</a></nav>
  <svg class="abs to-top" width="10" height="10" viewBox="0 0 10 10"><path d="M1 8l4-6 4 6" stroke="#e8493b" stroke-width="2" fill="none"/></svg>
  <div class="abs footer-rule"></div>
  <div class="abs copyright">© 2014 Crest Horn. All Right Reserved</div>
</body>
</html>
```